Business Card for Coastal Tundrabridge Advisory

We need a business card for Coastal Tundrabridge Advisory. The company website address is provided below. The company logo is attached. We provide specialized permafrost services to the mining, transportation, and oil & gas industries. The card should be prepared for:
Matthias Korhonen, PhD.
Coastal Tundrabridge Advisory
PO Box 418259
Quillwater, Alaska 99642
Direct: +1-907-555-0143
Email: mkorhonen@tundrabridgeadvisory.example
Website: www.coastaltundrabridgeadvisory.example

```html
<!DOCTYPE html>
<html lang="en">
<head>
<meta charset="utf-8">
<title>Coastal Tundrabridge Advisory – Business Card</title>
<link rel="stylesheet" href="https://fonts.googleapis.com/css2?family=Montserrat:wght@500;600;700&family=Lato:wght@400&display=swap">
<style>
  :root {
    --backdrop: #e8e8ea;
    --card-white: #ffffff;
    --ink: #161b22;
    --ink-soft: #2a2f36;
    --reverse-text: #ffffff;
  }
  * { margin: 0; padding: 0; box-sizing: border-box; }
  html, body { width: 1200px; height: 1108px; overflow: hidden; }
  body { background: var(--backdrop); position: relative; font-family: "Lato", sans-serif; color: var(--ink); }

  .card { position: absolute; width: 740px; height: 443px; overflow: hidden; }
  .card-front { left: 241px; top: 68px; background: var(--card-white); }
  .card-back { left: 248px; top: 589px; height: 442px; background: var(--ink); }

  .holder-name { position: absolute; left: 45px; top: 76px; font-family: "Montserrat", sans-serif; font-weight: 700; font-size: 22px; color: var(--ink); }
  .holder-title { position: absolute; left: 45px; top: 107px; font-family: "Montserrat", sans-serif; font-weight: 500; font-size: 15.5px; color: var(--ink-soft); }

  .company-name { position: absolute; right: 36px; top: 82px; width: 300px; text-align: right;
    font-family: "Montserrat", sans-serif; font-weight: 700; font-size: 21px; line-height: 1.2; letter-spacing: 1px; text-transform: uppercase; color: var(--ink); }

  .postal { position: absolute; left: 52px; top: 186px; font-size: 16.5px; line-height: 20px; color: var(--ink); }

  .contact-list { position: absolute; left: 50px; top: 258px; list-style: none; }
  .contact-list li { display: flex; align-items: center; height: 31px; font-size: 16px; color: var(--ink); }
  .contact-list svg { width: 16px; height: 16px; margin-right: 12px; fill: var(--ink); }

  .front-wave { position: absolute; left: 0; top: 0; width: 740px; height: 443px; }

  .back-pattern { position: absolute; inset: 0;
    background: linear-gradient(110deg, rgba(150,150,155,0.35) 0%, rgba(80,82,88,0.18) 30%, rgba(22,27,34,0) 60%); }
  .back-name { position: absolute; left: 0; right: 0; top: 338px; text-align: center;
    font-family: "Montserrat", sans-serif; font-weight: 700; font-size: 21px; letter-spacing: 1px; text-transform: uppercase; color: var(--reverse-text); }
</style>
</head>
<body>

<section class="card card-front">
  <svg class="front-wave" viewBox="0 0 740 443" aria-hidden="true">
    <path d="M0,322 C40,360 120,385 230,380 C380,372 560,330 740,318 L740,443 L0,443 Z" fill="var(--ink)"/>
    <path d="M0,356 C60,392 150,406 260,398 C420,388 580,346 740,331" fill="none" stroke="var(--card-white)" stroke-width="3"/>
  </svg>

  <h1 class="holder-name">Matthias Korhonen, PhD.</h1>
  <p class="holder-title">Managing Director</p>

  <p class="company-name">Coastal Tundrabridge Advisory</p>

  <address class="postal">PO Box 418259<br>Quillwater, Alaska 99642</address>

  <ul class="contact-list">
    <li>
      <svg viewBox="0 0 24 24" aria-hidden="true"><path d="M6.6 10.8a15.1 15.1 0 0 0 6.6 6.6l2.2-2.2c.3-.3.7-.4 1-.2 1.1.4 2.3.6 3.6.6.6 0 1 .4 1 1V20c0 .6-.4 1-1 1A17 17 0 0 1 3 4c0-.6.4-1 1-1h3.5c.6 0 1 .4 1 1 0 1.3.2 2.5.6 3.6.1.3 0 .7-.2 1z"/></svg>
      +1-907-555-0143
    </li>
    <li>
      <svg viewBox="0 0 24 24" aria-hidden="true"><path d="M3 5h18v14H3z M3 5l9 7 9-7" /></svg>
      mkorhonen@tundrabridgeadvisory.example
    </li>
    <li>
      <svg viewBox="0 0 24 24" aria-hidden="true"><circle cx="12" cy="12" r="10"/></svg>
      www.coastaltundrabridgeadvisory.example
    </li>
  </ul>
</section>

<section class="card card-back">
  <div class="back-pattern" role="img" aria-label="Faint repeated company-name pattern in glossy dark tones"></div>
  <p class="back-name">Coastal Tundrabridge Advisory</p>
</section>

</body>
</html>
```